Attractive door board for entrance beautysalon

Make an attractive design for a board that can be glued on the front door of a beauty salon. The salon location has no window in the front so I need something catchy and attractive. The door board contains a list of the services and the website: www.zaalmira.be, and the text "Enkel op afspraak, bel 0486391524"

Target Market(s)

woman between 16 and 99 years old

Industry/Entity Type

Beauty Salon

Font styles to use
Sans Serif

Requirements
Must have
• A very nice, attractive but sober design.
• It must have a classy Morvelle, Vasq, ... chique design.
• The logo must be on it (in attachment)
• There must be the following list in it:
• Gelaatsverzorging
• Wimperverlenging
• Wimperlifting
• Suikerontharing
• Permanente Make Up
• Airbrush Tanning
• Manicure - Pedicure - Nalkyn
• and then the website www.zaalmira.be, and the text "Enkel op afspraak, bel 0486391524"
Nice to have
• a catchy design,
• max. width can be 75 cm and max height 180 cm as it is a design for a board that will be glued on a door.
Should not have
• orchid flowers, buddha look a likes

```html
<!DOCTYPE html>
<html lang="nl">
<head>
<meta charset="utf-8">
<title>Zaal Mira – deurbord</title>
<link rel="stylesheet" href="https://fonts.googleapis.com/css2?family=Montserrat:wght@300;400&display=swap">
<style>
  :root {
    --board-black: #000000;
    --ink-white: #ffffff;
    --rule-grey: #5a5a5a;
    --skin-light: #f1d9c8;
    --skin-mid: #d9ae93;
    --skin-deep: #a87560;
    --backdrop-white: #ffffff;
  }
  * { margin: 0; padding: 0; box-sizing: border-box; }
  html, body {
    width: 1200px;
    height: 2880px;
    overflow: hidden;
    background: var(--board-black);
  }
  .door-board {
    position: relative;
    width: 1200px;
    height: 2880px;
    background: var(--board-black);
    color: var(--ink-white);
    font-family: "Montserrat", sans-serif;
    font-weight: 300;
    text-align: center;
  }
  .portrait-area {
    position: absolute;
    left: 160px;
    top: 212px;
    width: 864px;
    height: 936px;
    background:
      linear-gradient(90deg, var(--skin-deep) 0%, var(--skin-mid) 18%, var(--skin-light) 45%, var(--skin-light) 62%, var(--backdrop-white) 82%);
  }
  .salon-name {
    position: absolute;
    left: 0;
    width: 100%;
    top: 1530px;
    font-size: 58px;
    font-weight: 300;
    letter-spacing: 0.62em;
    padding-left: 0.62em;
    line-height: 1;
  }
  .divider {
    position: absolute;
    left: 140px;
    width: 920px;
    height: 2px;
    background: var(--rule-grey);
  }
  .divider--upper { top: 1788px; }
  .divider--lower { top: 2120px; }
  .contact {
    position: absolute;
    left: 0;
    width: 100%;
    top: 1950px;
    font-size: 38px;
    letter-spacing: 0.12em;
    line-height: 58px;
  }
  .services {
    position: absolute;
    left: 0;
    width: 100%;
    top: 2204px;
    list-style: none;
    font-size: 35px;
    letter-spacing: 0.2em;
    line-height: 42px;
    text-transform: uppercase;
  }
</style>
</head>
<body>
  <main class="door-board">
    <div class="portrait-area" role="img" aria-label="Beautyfoto van een verzorgde huid tegen een witte achtergrond"></div>

    <h1 class="salon-name">ZAAL MIRA</h1>

    <div class="divider divider--upper"></div>

    <p class="contact">
      WWW.ZAALMIRA.BE<br>
      ENKEL OP AFSPRAAK, BEL 0486391524
    </p>

    <div class="divider divider--lower"></div>

    <ul class="services">
      <li>Gelaatsverzorging</li>
      <li>Wimperverlenging</li>
      <li>Wimperlifting</li>
      <li>Suikerontharing</li>
      <li>Permanente Make Up</li>
      <li>Airbrush Tanning</li>
      <li>Manicure - Pedicure - Nalkyn</li>
    </ul>
  </main>
</body>
</html>
```